Revamp Of Landing Page For an Automated AI Voice Agents Agency

here is my current landing page https://app.brightfernpromotionhub.biz/v2/preview/WXKRPmQ4hLzYBvNdTeGS?notrack=true

Please use all my current content and imagery of ai agents in your new design. Make it easy to ready, easy to navigate and easy to understand

I am looking for a SLEEK shiny polished looking website. I like Dark themed sites but am open to see light themed sites too so please dont be shy.

The site should have an Ai Voice Agent Theme about it. Maybe look and feel of futureistic but simple and not intimidating to the average person...

Here are a couple website designs I like for reference:
https://q7v.io/
https://ai-bots.marekholvin.com/
https://chatwelmo.com/ai-agents

Target Market(s)

b2b

Industry/Entity Type

AI Voice Agents

Coding

Coded - Design and coding required

Font styles to use
Other font styles liked:
• open

Requirements
Must have
• all elements and content and images used in existing design.
Nice to have
• open
Should not have
• open

```html
<!DOCTYPE html>
<html lang="en">
<head>
<meta charset="UTF-8">
<title>Auralink – AI Voice Agents</title>
<link href="https://fonts.googleapis.com/css2?family=Poppins:ital,wght@0,400;0,500;0,600;0,700;0,800;1,400;1,500&display=swap" rel="stylesheet">
<style>
:root{
  --navy:#17146b;
  --navy-deep:#120f55;
  --card-navy:#2a25a6;
  --yellow:#f7b500;
  --yellow-text:#2a1a00;
  --orange-accent:#f7a21b;
  --white:#ffffff;
  --soft:#d9d6ff;
}
*{box-sizing:border-box;margin:0;padding:0}
html,body{width:1200px;height:5146px;overflow:hidden}
body{font-family:'Poppins',sans-serif;color:var(--white);background:var(--navy)}
section{position:relative;width:1200px;overflow:hidden}
h1,h2,h3{font-weight:800;letter-spacing:.5px}

.logo{display:flex;align-items:center;justify-content:center;gap:12px;font-size:36px;font-weight:500;letter-spacing:4px;color:var(--white)}
.logo-dot{width:30px;height:30px;border:3px solid var(--white);border-radius:50%}

.btn{display:inline-block;background:var(--yellow);color:var(--yellow-text);font-weight:700;font-size:22px;text-align:center;padding:10px 0;border-radius:2px;text-decoration:none}
.note{font-style:italic;font-size:12.5px;line-height:24px;color:var(--soft)}

/* hero */
.hero{height:720px;background:linear-gradient(110deg,#3b25c9 0%,#4a2fe6 45%,#5b45f2 100%)}
.hero .logo{position:absolute;top:40px;left:0;right:0;z-index:2}
.hero-art{position:absolute;right:0;top:0;width:520px;height:720px;background:radial-gradient(ellipse at 60% 40%,#9aa3ff 0%,#5d58e8 35%,#3b2bc7 75%,transparent 100%)}
.hero-copy{position:absolute;left:76px;top:164px;width:610px}
.hero-copy h1{font-size:35px;line-height:42px;font-weight:800}
.hero-copy .btn{width:420px;margin-top:28px}
.hero-copy .note{margin-top:18px;width:600px}

/* workforce */
.workforce{height:1456px;background:var(--navy)}
.section-title{text-align:center;font-size:48px;padding-top:72px}
.agent-card{position:absolute;border-radius:6px;overflow:hidden;padding:30px 16px}
.agent-card h3{font-size:32px;line-height:34px;font-weight:800;position:relative}
.agent-card .tag{font-size:13.5px;font-weight:700;line-height:26px;margin-top:10px;position:relative}
.agent-card p{font-size:14px;line-height:26px;color:#ece9ff;margin-top:12px;position:relative}
.agent-art{position:absolute;border-radius:50%}
.card-sales{left:76px;top:190px;width:512px;height:336px;background:linear-gradient(135deg,#4a36d8,#7b32d6)}
.card-reception{left:616px;top:190px;width:512px;height:336px;background:linear-gradient(135deg,#1e8f45,#27ab57)}
.card-qualifier{left:76px;top:552px;width:1052px;height:334px;background:linear-gradient(135deg,#b84d1a,#d0642a)}
.card-setter{left:76px;top:914px;width:512px;height:336px;background:linear-gradient(135deg,#3d44d8,#6b3fd8)}
.card-followup{left:616px;top:914px;width:512px;height:336px;background:linear-gradient(135deg,#6b36d0,#8a46d6)}
.card-sales .copy,.card-setter .copy{width:270px}
.card-reception .copy,.card-followup .copy{width:320px}
.card-qualifier .copy{width:680px;padding-top:54px}
.card-reception .copy p,.card-followup .copy p{font-size:13.5px}
.workforce .btn{position:absolute;left:390px;top:1300px;width:422px}
.workforce .note{position:absolute;left:140px;top:1372px;width:920px;text-align:center}

/* wish */
.wish{height:436px;background:linear-gradient(100deg,#2f2ec6 0%,#4a34dc 60%,#2a1f9a 100%)}
.wish-art{position:absolute;right:60px;top:0;width:400px;height:436px;background:radial-gradient(ellipse at 55% 50%,#8d7dff 0%,#5a3fe0 40%,transparent 75%)}
.wish-copy{position:absolute;left:76px;top:60px;width:600px}
.wish-copy h2{font-size:48px;line-height:50px}
.wish-copy .kicker{color:var(--orange-accent);font-weight:700;font-size:22px;margin-top:12px}
.wish-copy .lead{font-size:24px;line-height:34px;margin-top:6px;width:540px}
.wish-copy p{font-size:14px;line-height:26px;margin-top:14px;color:#ece9ff}

/* employee */
.employee{height:488px;background:var(--navy)}
.employee h2{text-align:center;font-size:48px;line-height:60px;padding-top:60px}
.feature{position:absolute;top:196px;width:328px;height:212px;background:var(--card-navy);border-radius:4px;text-align:center;padding-top:26px}
.feature svg{width:64px;height:64px}
.feature h4{font-size:21px;font-weight:700;margin-top:14px}
.feature p{font-size:13px;line-height:24px;color:var(--soft);margin-top:8px}

/* hired */
.hired{height:496px;background:linear-gradient(110deg,#4024c9 0%,#3b2ae2 60%,#2b1eae 100%)}
.hired-art{position:absolute;left:80px;top:44px;width:300px;height:410px;background:radial-gradient(ellipse at 50% 45%,#e8ecf6 0%,#aab6d8 35%,#5c4fd8 70%,transparent 90%)}
.hired-copy{position:absolute;left:434px;top:54px;width:690px}
.hired-copy h2{font-size:48px;line-height:54px}
.hired-copy .kicker{color:var(--orange-accent);font-weight:700;font-size:22px;margin-top:6px}
.hired-copy .lead{font-size:24px;line-height:34px;margin-top:4px;width:540px}
.hired-copy .btn{width:422px;margin-top:12px}
.hired-copy .note{margin-top:10px}

/* faq */
.faq{height:490px;background:var(--navy)}
.faq-list{position:absolute;left:76px;top:60px;width:654px}
.faq-list h2{font-size:48px}
.faq-item{display:flex;justify-content:space-between;align-items:center;font-size:20px;padding:22px 0;border-bottom:1px solid #3c36a8}
.faq-item.open{border:none;padding:18px 0 6px;color:var(--orange-accent)}
.faq-answer{font-style:italic;font-size:13px;line-height:24px;padding-bottom:20px;border-bottom:1px solid #3c36a8}
.faq-answer span{display:block;width:570px}
.faq-icon{width:20px;height:20px;flex:none}
.review-box{position:absolute;left:796px;top:76px;width:332px;height:340px;background:var(--card-navy);border-radius:4px;text-align:center;padding-top:30px}
.review-box h3{font-size:29px;line-height:39px;font-weight:700}
.stars{display:flex;justify-content:center;gap:12px;margin-top:12px}
.stars svg{width:32px;height:32px}

/* promise */
.promise{height:276px;background:var(--navy-deep)}
.promise h2{position:absolute;left:76px;top:80px;font-size:48px;line-height:56px}
.promise-card{position:absolute;top:42px;width:298px;height:190px;background:var(--card-navy);border-radius:4px;text-align:center;padding-top:30px}
.promise-card svg{width:48px;height:48px}
.promise-card h4{font-size:20px;font-weight:700;line-height:28px;margin-top:14px}
.promise-card p{font-size:13px;line-height:20px;color:var(--soft);margin-top:4px}

/* cta */
.cta{height:444px;background:linear-gradient(110deg,#2c22c4 0%,#4a3cf0 50%,#3022c8 100%);text-align:center}
.cta h2{font-size:48px;line-height:58px;padding-top:70px;width:1000px;margin:0 auto}
.cta .btn{width:422px;margin-top:28px}
.cta .note{width:1100px;margin:14px auto 0}

/* footer */
.footer{height:340px;background:var(--navy);text-align:center;font-size:12px;line-height:28px;color:var(--soft)}
.footer .logo{padding-top:60px;margin-bottom:16px}
.footer .links{color:var(--white)}
</style>
</head>
<body>

<section class="hero">
  <div class="hero-art" role="img" aria-label="Futuristic humanoid robot wearing a headset microphone"></div>
  <div class="logo"><span class="logo-dot"></span>AURALINK</div>
  <div class="hero-copy">
    <h1>Ai Voice Agents That Answer Calls, Book Appts, Send Emails, Text Messages, Follow Up Reminders, Transfer Calls &amp; More For You 24 Hours 7 Days A Week!</h1>
    <a class="btn" href="#">Get An Instant Free Demo</a>
    <p class="note">We Will Create An Ai Agent Customized For Your Business At No Cost. Simply Click The Button Above And Your Very Own Ai Agent Will Be Calling You In Just A Couple Minutes. Experience The Magic And Get Ready To Be Very Impressed!</p>
  </div>
</section>

<section class="workforce">
  <h2 class="section-title">Meet Your New AI-Powered Workforce</h2>

  <article class="agent-card card-sales">
    <div class="agent-art" role="img" aria-label="Purple robot sales agent" style="right:10px;top:20px;width:180px;height:300px;background:radial-gradient(ellipse,#9b6dff,#6a3ad8 60%,transparent 75%)"></div>
    <div class="copy">
      <h3>Ai Sales<br>Agent</h3>
      <p>Dorian will take your inbound sales calls. Will give all detailed information to the customer, answer questions in a normal conversational tone and can book sales appointments or transfer hot prospects to a human to close the sale.</p>
    </div>
  </article>

  <article class="agent-card card-reception">
    <div class="agent-art" role="img" aria-label="White receptionist robot with a speech bubble" style="right:0;top:20px;width:150px;height:300px;background:radial-gradient(ellipse,#e6f3ee,#8fd0a8 45%,transparent 75%)"></div>
    <div class="copy">
      <h3>Ai Receptionist</h3>
      <p class="tag">Takes Overflow and After Hours Calls or Can Take Calls 24/7 &amp; Transfer To Appropriate Dept.</p>
      <p>Milo handles all your calls 24/7. You can also set him to only take overflow calls and after hours. He can send emails and sms messages and even book appointments over the call</p>
    </div>
  </article>

  <article class="agent-card card-qualifier">
    <div class="agent-art" role="img" aria-label="Orange robot working on a laptop with chat bubbles" style="right:20px;top:10px;width:340px;height:320px;background:radial-gradient(ellipse,#f09a3c,#d86a22 50%,transparent 75%)"></div>
    <div class="copy">
      <h3>Ai Lead Qualifier</h3>
      <p class="tag">Conversate With Prospects To Qualify Before Handing Over To Sales Team</p>
      <p>All of our ai agents gather information and qualify leads. If they are interested in the services on the call then our ai agents will assist them with booking an appointment with our sales team over the call.</p>
    </div>
  </article>

  <article class="agent-card card-setter">
    <div class="agent-art" role="img" aria-label="White robot typing on a laptop" style="right:0;top:20px;width:190px;height:300px;background:radial-gradient(ellipse,#eef0f8,#a7a6e6 45%,transparent 75%)"></div>
    <div class="copy">
      <h3>Ai Appointment<br>Setter</h3>
      <p class="tag">Book Appts &amp; Reservations On Auto Pilot</p>
      <p>Reggie offers business advice, helps brainstorm ideas, and provides insights on growth tactics to support your entrepreneurial journey.</p>
    </div>
  </article>

  <article class="agent-card card-followup">
    <div class="agent-art" role="img" aria-label="Small standing robot with a message bubble" style="right:10px;top:20px;width:160px;height:300px;background:radial-gradient(ellipse,#e4e6f2,#a27fe0 45%,transparent 75%)"></div>
    <div class="copy">
      <h3>Ai Follow Up<br>Reminders</h3>
      <p class="tag">Calls, Sends SMS &amp; Email<br>Reminders</p>
      <p>Tessa handles all the follow up calls, appt reminders and sends out the email and sms reminders too.</p>
    </div>
  </article>

  <a class="btn" href="#">Get An Instant Free Demo</a>
  <p class="note">We Will Create An Ai Agent Customized For Your Business At No Cost. Simply Click The Button Above And Your Very Own Ai Agent Will Be Calling You In Just A Couple Minutes. Experience The Magic And Get Ready To Be Very Impressed!</p>
</section>

<section class="wish">
  <div class="wish-art" role="img" aria-label="Humanoid robot holding a glowing smartphone"></div>
  <div class="wish-copy">
    <h2>Your Wish Is Their<br>Command</h2>
    <p class="kicker">Install the power of AI for your business</p>
    <p class="lead">Your New Ai Agents Will Never Call In Sick And Will Never Complain!</p>
    <p>With your new team of AI Agents, handling inbound calls, sending emails and sms messages, booking appointments and handling customer service inquiries is going to save you a ton of time and money.</p>
  </div>
</section>

<section class="employee">
  <h2>An Employee<br>That Never Gets Sick!</h2>
  <div class="feature" style="left:76px">
    <svg viewBox="0 0 64 64" fill="none" stroke="#fff" stroke-width="2"><path d="M32 10c-6-4-14 0-14 6-6 1-8 8-4 12-4 4-2 12 4 13 0 6 8 10 14 6V10z"/><path d="M32 10c6-4 14 0 14 6 6 1 8 8 4 12 4 4 2 12-4 13 0 6-8 10-14 6"/><path d="M32 20h8M32 32h10M32 44h6M24 24v8M24 36h-4"/><circle cx="40" cy="20" r="2"/><circle cx="42" cy="32" r="2"/></svg>
    <h4>Trained In Seconds</h4>
    <p>Learns Your Entire Website<br>In Seconds</p>
  </div>
  <div class="feature" style="left:438px">
    <svg viewBox="0 0 64 64" fill="none" stroke="#fff" stroke-width="2"><circle cx="32" cy="32" r="22"/><ellipse cx="32" cy="32" rx="10" ry="22"/><path d="M10 32h44M14 20h36M14 44h36M32 10v44"/></svg>
    <h4>Worldwide</h4>
    <p>Works Anywhere In The Globe</p>
  </div>
  <div class="feature" style="left:800px">
    <svg viewBox="0 0 64 64" fill="none" stroke="#fff" stroke-width="2.5"><circle cx="28" cy="20" r="10"/><path d="M10 54c0-12 8-20 18-20 4 0 7 1 10 3"/><path d="M38 46l6 6 12-14"/></svg>
    <h4>User-Friendly</h4>
    <p>Your Ai Agents Sound As If They're<br>Real Humans</p>
  </div>
</section>

<section class="hired">
  <div class="hired-art" role="img" aria-label="White robot holding a tablet"></div>
  <div class="hired-copy">
    <h2>Our Ai Agents<br>Our Ready To Be Hired</h2>
    <p class="kicker">Lightning-Fast Responses</p>
    <p class="lead">Instant answers, no coffee, bathroom or lunch breaks needed.</p>
    <a class="btn" href="#">Get An Instant Free Demo</a>
    <p class="note">We Will Create An Ai Agent Customized For Your Business At No Cost. Simply Click The Button Above And Your Very Own Ai Agent Will Be Calling You In Just A Couple Minutes. Experience The Magic And Get Ready To Be Very Impressed!</p>
  </div>
</section>

<section class="faq">
  <div class="faq-list">
    <h2>Do You Have Questions?</h2>
    <div class="faq-item open">What exactly are the AI Voice Agents?
      <svg class="faq-icon" viewBox="0 0 20 20"><circle cx="10" cy="10" r="10" fill="#f7a21b"/><path d="M5 10h10" stroke="#17146b" stroke-width="2.5"/></svg>
    </div>
    <p class="faq-answer"><span>AI Voice Agents are specialized human sounding bots, having smart and masterful conversations and each is expertly trained in seconds for a specific business function.</span></p>
    <div class="faq-item">How will these AI Voice Agents benefit?
      <svg class="faq-icon" viewBox="0 0 20 20"><circle cx="10" cy="10" r="10" fill="#fff"/><path d="M5 10h10M10 5v10" stroke="#17146b" stroke-width="2.5"/></svg>
    </div>
    <div class="faq-item" style="border:none">Are they easy to use?
      <svg class="faq-icon" viewBox="0 0 20 20"><circle cx="10" cy="10" r="10" fill="#fff"/><path d="M5 10h10M10 5v10" stroke="#17146b" stroke-width="2.5"/></svg>
    </div>
  </div>
  <aside class="review-box">
    <h3>After Our<br>Customers Have<br>A Conversation<br>With Their New Ai<br>Voice Agent They<br>Give Us 5 Stars!</h3>
    <div class="stars">
      <svg viewBox="0 0 24 24"><path d="M12 1l3.4 7 7.6 1-5.5 5.3 1.3 7.7L12 18.3 5.2 22l1.3-7.7L1 9l7.6-1z" fill="#f7a21b"/></svg>
      <svg viewBox="0 0 24 24"><path d="M12 1l3.4 7 7.6 1-5.5 5.3 1.3 7.7L12 18.3 5.2 22l1.3-7.7L1 9l7.6-1z" fill="#f7a21b"/></svg>
      <svg viewBox="0 0 24 24"><path d="M12 1l3.4 7 7.6 1-5.5 5.3 1.3 7.7L12 18.3 5.2 22l1.3-7.7L1 9l7.6-1z" fill="#f7a21b"/></svg>
      <svg viewBox="0 0 24 24"><path d="M12 1l3.4 7 7.6 1-5.5 5.3 1.3 7.7L12 18.3 5.2 22l1.3-7.7L1 9l7.6-1z" fill="#f7a21b"/></svg>
      <svg viewBox="0 0 24 24"><path d="M12 1l3.4 7 7.6 1-5.5 5.3 1.3 7.7L12 18.3 5.2 22l1.3-7.7L1 9l7.6-1z" fill="#f7a21b"/></svg>
    </div>
  </aside>
</section>

<section class="promise">
  <h2>Our Promise<br>To You</h2>
  <div class="promise-card" style="left:498px">
    <svg viewBox="0 0 48 48" fill="none" stroke="#fff" stroke-width="2.5"><rect x="6" y="10" width="36" height="32" rx="3"/><path d="M6 18h36M15 5v9M33 5v9"/><path d="M14 26h4M22 26h4M30 26h4M14 34h4M22 34h4M30 34h4" stroke-width="3"/></svg>
    <h4>14-day money-back<br>guarantee*</h4>
  </div>
  <div class="promise-card" style="left:828px">
    <svg viewBox="0 0 48 48" fill="none" stroke="#fff" stroke-width="2.5"><path d="M8 22c0-8 7-14 16-14s16 6 16 14-7 14-16 14c-3 0-5-.5-7-1.3L9 38l2-6c-2-2.5-3-6-3-10z"/><path d="M17 22h14M17 28h9"/></svg>
    <h4>24/7 Customer Support</h4>
    <p>Often praised for our friendly<br>&amp; helpful support team.</p>
  </div>
</section>

<section class="cta">
  <h2>These AI Agents Can Help Your Business Tremendously. Imagine The Possibilities</h2>
  <a class="btn" href="#">Get An Instant Free Demo</a>
  <p class="note">We Will Create An Ai Agent Customized For Your Business At No Cost. Simply Click The Button Above And Your Very Own Ai Agent Will Be Calling You In Just A Couple Minutes. Experience The Magic And Get Ready To Be Very Impressed!</p>
</section>

<footer class="footer">
  <div class="logo"><span class="logo-dot"></span>AURALINK</div>
  <p>© 2025 Auralink</p>
  <p>*14-Day Money Back Guarantee Terms: If you use the ai agents and you're not happy. Then you can contact us in the first 14 days for a full refund.</p>
  <p>DISCLAIMER:</p>
  <p class="links">PRIVACY | TERMS &amp; CONDITIONS | EARNINGS &amp; PRODUCTS DISCLAIMER</p>
  <p>Do you have questions about ( ) Please email ( )</p>
  <p>IMPORTANT: This site is not a part of the Circlebook website or Circlebook Inc. Additionally, this site is NOT endorsed by Circlebook in any way.</p>
  <p>CIRCLEBOOK is a trademark of CIRCLEBOOK, Inc.</p>
</footer>

</body>
</html>
```